Stonebridge Building and Projects business cards

A business card with watermark background (construction work)

Company logo attached

Home improvement projects
House renovations
Bathroom and kitchen renovations
House extensions
New builds and granny flats

Director Omar Haddani
(Phone number)
omar@sbpbuilding.com.au
(Instagram logo) sbp_building

```html
<!DOCTYPE html>
<html lang="en">
<head>
<meta charset="utf-8">
<title>Stonebridge Building and Projects – Business Cards</title>
<link rel="stylesheet" href="https://fonts.googleapis.com/css2?family=Montserrat:wght@700&family=Roboto:wght@400;500;700&display=swap">
<style>
  :root {
    --brand-blue: #0d74bf;
    --ink: #3a3a3a;
    --ink-soft: #555;
    --card-white: #f7f7f7;
    --stripe-grey: #3d4044;
    --page-bg: #e4e5e7;
    --mark-grey: #e9e9ea;
  }
  * { margin: 0; padding: 0; box-sizing: border-box; }
  html, body { width: 1200px; height: 1050px; overflow: hidden; }
  body {
    background: var(--page-bg);
    font-family: "Roboto", Arial, sans-serif;
    color: var(--ink);
    position: relative;
  }
  .card {
    position: absolute;
    left: 290px;
    width: 620px;
    height: 360px;
    border-radius: 24px;
    background: var(--card-white);
    overflow: hidden;
    box-shadow: 0 6px 18px rgba(0,0,0,0.18);
  }
  .card--front { top: 115px; }
  .card--back { top: 575px; }
  .card__shapes { position: absolute; inset: 0; width: 100%; height: 100%; }
  .watermark {
    position: absolute;
    border-radius: 6px;
    background: linear-gradient(135deg, rgba(220,221,223,0.0), var(--mark-grey) 45%, rgba(220,221,223,0.0));
  }
  .card--front .watermark { left: 300px; top: 20px; width: 300px; height: 270px; }
  .card--back .watermark { left: 380px; top: 60px; width: 220px; height: 260px; }

  .wordmark {
    position: absolute;
    display: flex;
    align-items: center;
    gap: 12px;
    font-family: "Montserrat", Arial, sans-serif;
    font-weight: 700;
    line-height: 1.2;
  }
  .wordmark__square { width: 20px; height: 20px; flex: none; }
  .wordmark__name { font-size: 22px; white-space: nowrap; }
  .card--front .wordmark { left: 44px; top: 132px; color: var(--brand-blue); }
  .card--front .wordmark__square { background: var(--brand-blue); }
  .card--back .wordmark { left: 38px; top: 132px; color: #fff; }
  .card--back .wordmark__square { background: #fff; }

  .services {
    position: absolute;
    left: 320px;
    top: 62px;
    list-style: none;
    font-size: 17px;
    line-height: 1.55;
    color: var(--ink);
  }
  .services li { display: flex; align-items: flex-start; gap: 14px; }
  .services__bullet { flex: none; margin-top: 8px; width: 10px; height: 10px; }

  .social-tab {
    position: absolute;
    left: 290px;
    bottom: 16px;
    display: flex;
    align-items: center;
    gap: 10px;
    color: #fff;
    font-size: 16px;
  }

  .person { position: absolute; left: 352px; top: 82px; }
  .person__name { font-size: 26px; font-weight: 700; color: var(--brand-blue); }
  .person__role { font-size: 16px; color: var(--ink-soft); margin-top: 2px; }
  .contacts { list-style: none; position: absolute; left: 352px; top: 168px; font-size: 16px; line-height: 1.6; color: var(--ink); }
  .contacts li { display: flex; align-items: center; gap: 12px; }
  .contacts svg { width: 16px; height: 16px; flex: none; }
</style>
</head>
<body>

<section class="card card--front" aria-label="Business card front">
  <div class="watermark" role="img" aria-label="Faint construction work watermark"></div>
  <svg class="card__shapes" viewBox="0 0 620 360" aria-hidden="true">
    <path d="M268 360 L268 322 Q268 306 284 306 L560 306 Q596 306 620 280 L620 360 Z" fill="var(--brand-blue)"/>
  </svg>

  <div class="wordmark">
    <span class="wordmark__square"></span>
    <span class="wordmark__name">Stonebridge<br>Building and<br>Projects</span>
  </div>

  <ul class="services">
    <li><svg class="services__bullet" viewBox="0 0 10 10"><rect x="0" y="0" width="4" height="4" fill="var(--brand-blue)"/><rect x="6" y="0" width="4" height="4" fill="var(--brand-blue)"/><rect x="0" y="6" width="4" height="4" fill="var(--brand-blue)"/><rect x="6" y="6" width="4" height="4" fill="var(--brand-blue)"/></svg>Home improvement projects</li>
    <li><svg class="services__bullet" viewBox="0 0 10 10"><rect x="0" y="0" width="4" height="4" fill="var(--brand-blue)"/><rect x="6" y="0" width="4" height="4" fill="var(--brand-blue)"/><rect x="0" y="6" width="4" height="4" fill="var(--brand-blue)"/><rect x="6" y="6" width="4" height="4" fill="var(--brand-blue)"/></svg>House renovations</li>
    <li><svg class="services__bullet" viewBox="0 0 10 10"><rect x="0" y="0" width="4" height="4" fill="var(--brand-blue)"/><rect x="6" y="0" width="4" height="4" fill="var(--brand-blue)"/><rect x="0" y="6" width="4" height="4" fill="var(--brand-blue)"/><rect x="6" y="6" width="4" height="4" fill="var(--brand-blue)"/></svg>Bathroom and kitchen<br>renovations</li>
    <li><svg class="services__bullet" viewBox="0 0 10 10"><rect x="0" y="0" width="4" height="4" fill="var(--brand-blue)"/><rect x="6" y="0" width="4" height="4" fill="var(--brand-blue)"/><rect x="0" y="6" width="4" height="4" fill="var(--brand-blue)"/><rect x="6" y="6" width="4" height="4" fill="var(--brand-blue)"/></svg>House extensions</li>
    <li><svg class="services__bullet" viewBox="0 0 10 10"><rect x="0" y="0" width="4" height="4" fill="var(--brand-blue)"/><rect x="6" y="0" width="4" height="4" fill="var(--brand-blue)"/><rect x="0" y="6" width="4" height="4" fill="var(--brand-blue)"/><rect x="6" y="6" width="4" height="4" fill="var(--brand-blue)"/></svg>New builds and granny flats</li>
  </ul>

  <div class="social-tab">
    <svg width="16" height="16" viewBox="0 0 16 16" aria-hidden="true"><circle cx="8" cy="8" r="6.5" fill="none" stroke="#fff" stroke-width="1.8"/></svg>
    <span>sbp_building</span>
  </div>
</section>

<section class="card card--back" aria-label="Business card back">
  <div class="watermark" role="img" aria-label="Faint construction work watermark"></div>
  <svg class="card__shapes" viewBox="0 0 620 360" aria-hidden="true">
    <path d="M0 0 L200 0 Q370 170 250 360 L0 360 Z" fill="var(--stripe-grey)"/>
    <path d="M0 0 L186 0 Q352 170 234 360 L0 360 Z" fill="var(--brand-blue)"/>
  </svg>

  <div class="wordmark">
    <span class="wordmark__square"></span>
    <span class="wordmark__name">Stonebridge<br>Building and<br>Projects</span>
  </div>

  <div class="person">
    <div class="person__name">Omar Haddani</div>
    <div class="person__role">Managing Director</div>
  </div>

  <ul class="contacts">
    <li><svg viewBox="0 0 16 16" aria-hidden="true"><circle cx="8" cy="8" r="7" fill="none" stroke="var(--stripe-grey)" stroke-width="1.3"/><path d="M5.5 4.5 L7 6 L6.2 7.2 Q7 8.8 8.8 9.8 L10 9 L11.5 10.5 L10.6 11.5 Q7 11 4.6 6.4 Z" fill="var(--stripe-grey)"/></svg>0400 318 726</li>
    <li><svg viewBox="0 0 16 16" aria-hidden="true"><rect x="1.5" y="3.5" width="13" height="9" fill="none" stroke="var(--stripe-grey)" stroke-width="1.3"/><path d="M1.5 3.5 L8 9 L14.5 3.5" fill="none" stroke="var(--stripe-grey)" stroke-width="1.3"/></svg>omar@sbpbuilding.com.au</li>
    <li><svg viewBox="0 0 16 16" aria-hidden="true"><circle cx="8" cy="8" r="6.5" fill="none" stroke="var(--stripe-grey)" stroke-width="1.3"/><ellipse cx="8" cy="8" rx="3" ry="6.5" fill="none" stroke="var(--stripe-grey)" stroke-width="1.1"/><line x1="1.5" y1="8" x2="14.5" y2="8" stroke="var(--stripe-grey)" stroke-width="1.1"/></svg>sbpbuilding.com.au</li>
    <li><svg viewBox="0 0 16 16" aria-hidden="true"><circle cx="8" cy="8" r="6.5" fill="none" stroke="var(--stripe-grey)" stroke-width="1.3"/></svg>sbp_building</li>
  </ul>
</section>

</body>
</html>
```